Business Card Design for Software Development Company

I am looking for a business card design the incorporates my new logo (attached below).

Key information to include:
Name: Martin Quelbrook
Title: CEO
Email: martin@brightwellcivic.example
Phone: 555-218-9403
Website: www.brightwellcivic.example

NOTE: This design should be easy to edit so that we can order cards for different members of our team.

```html
<!DOCTYPE html>
<html lang="en">
<head>
<meta charset="utf-8">
<title>BrightwellLabs Business Card</title>
<link rel="stylesheet" href="https://fonts.googleapis.com/css2?family=Montserrat:wght@400;600;700&display=swap">
<style>
  :root {
    --page-bg: #151515;
    --card-bg: #1f1f1f;
    --white: #f4f4f4;
    --teal: #1aa890;
    --orange: #e6782a;
    --muted: #d8d8d8;
  }
  * { box-sizing: border-box; margin: 0; padding: 0; }
  html, body {
    width: 1200px; height: 1059px; overflow: hidden;
    background: var(--page-bg);
    font-family: "Montserrat", Arial, sans-serif;
  }
  .canvas { position: relative; width: 1200px; height: 1059px; }
  .card {
    position: absolute;
    background: var(--card-bg);
    border-radius: 18px;
  }
  .card--front { left: 257px; top: 89px; width: 687px; height: 390px; }
  .card--back  { left: 254px; top: 547px; width: 693px; height: 393px; }

  .brand {
    position: absolute; left: 0; right: 0;
    display: flex; flex-direction: column; align-items: center;
  }
  .brand__row { display: flex; align-items: center; gap: 12px; }
  .brand__mark { background: var(--orange); flex: none; }
  .brand__name { color: var(--white); font-weight: 700; letter-spacing: -0.5px; line-height: 1; }
  .brand__tagline {
    align-self: flex-end; color: var(--white); font-weight: 600;
    letter-spacing: 0.3px; text-transform: uppercase; margin-top: 4px;
  }

  .card--front .brand { top: 84px; }
  .card--front .brand__row { width: 440px; margin: 0 auto; }
  .card--front .brand__mark { width: 26px; height: 26px; }
  .card--front .brand__name { font-size: 47px; }
  .card--front .brand__tagline { font-size: 7px; margin-right: calc(50% - 220px); }

  .card--back .brand { top: 160px; }
  .card--back .brand__row { width: 520px; margin: 0 auto; }
  .card--back .brand__mark { width: 32px; height: 32px; }
  .card--back .brand__name { font-size: 56px; }
  .card--back .brand__tagline { font-size: 8.5px; margin-right: calc(50% - 260px); }

  .person {
    position: absolute; right: 368px; top: 262px; text-align: right;
  }
  .person__name { font-size: 25px; font-weight: 700; line-height: 1.1; white-space: nowrap; }
  .person__first { color: var(--teal); }
  .person__last { color: var(--orange); }
  .person__title { color: var(--white); font-size: 16px; font-weight: 400; margin-top: 2px; }

  .divider {
    position: absolute; left: 342px; top: 251px; width: 1px; height: 66px;
    background: var(--teal);
  }

  .contacts {
    position: absolute; left: 369px; top: 242px; list-style: none;
  }
  .contacts__item {
    display: flex; align-items: center; gap: 8px;
    color: var(--muted); font-size: 16.5px; height: 28px; white-space: nowrap;
  }
  .contacts__icon { width: 11px; height: 11px; flex: none; }
</style>
</head>
<body>
<div class="canvas">
  <section class="card card--front">
    <div class="brand">
      <div class="brand__row">
        <span class="brand__mark"></span>
        <span class="brand__name">BrightwellLabs</span>
      </div>
      <span class="brand__tagline">A Division of Brightwell Civic</span>
    </div>

    <div class="person">
      <p class="person__name"><span class="person__first">Martin</span> <span class="person__last">Quelbrook</span></p>
      <p class="person__title">CEO</p>
    </div>

    <span class="divider"></span>

    <ul class="contacts">
      <li class="contacts__item">
        <svg class="contacts__icon" viewBox="0 0 12 12" aria-hidden="true"><path fill="#e6782a" d="M1 4.5C1 2.5 3.5 2 6 2s5 .5 5 2.5v1H8.5V4.3H3.5v1.2H1zM2.5 6h7l1 4.5h-9z"/></svg>
        <span>555-218-9403</span>
      </li>
      <li class="contacts__item">
        <svg class="contacts__icon" viewBox="0 0 12 12" aria-hidden="true"><path fill="#e6782a" d="M1 5l5-4 5 4v6H1z"/><path fill="none" stroke="#1f1f1f" stroke-width="1" d="M1 5l5 3.5L11 5"/></svg>
        <span>martin@brightwellcivic.example</span>
      </li>
      <li class="contacts__item">
        <svg class="contacts__icon" viewBox="0 0 12 12" aria-hidden="true"><circle cx="6" cy="6" r="5.5" fill="#e6782a"/><path fill="none" stroke="#1f1f1f" stroke-width="0.9" d="M6 .5v11M.5 6h11M6 .5c-3 3-3 8 0 11M6 .5c3 3 3 8 0 11"/></svg>
        <span>www.brightwellcivic.example</span>
      </li>
    </ul>
  </section>

  <section class="card card--back">
    <div class="brand">
      <div class="brand__row">
        <span class="brand__mark"></span>
        <span class="brand__name">BrightwellLabs</span>
      </div>
      <span class="brand__tagline">A Division of Brightwell Civic</span>
    </div>
  </section>
</div>
</body>
</html>
```